Quality Monitoring Company Needs a New Site

We are an established company that has a fair number of clients but the site lacks current design standards that we'd like to keep up with. We'd like to mimic the same style of the site on plinkora.com, vetrumo.com, https://brindlecoffer.com/, etc. We'd also like to make sure the designer understands SEO Silos and how it effects the design elements. Attached is the structure that I'd like to follow for the pages. You don't need to design every single sub-page because they'll probably be fairly similar; however, I want to see at least 1 each. Please use the content on our current site for filler areas. Please try to do a good job of understanding what we do so you can use your best judgement on what is needed to be successful. Use our color scheme and the logo should be the side view but I included the AI just in case.
Updates

I am narrowing down on the field of designs that I have received. There are a lot of similarities between the designs I like and don't like. I'd also like to ensure that some of the inner pages get done in the next 5 days so I can see the creativity that is there as well. That is probably what is next -- getting a few inner pages completed so I can see what you can come up with (not based on our current website) because the current "front pages" are all so good and so close.

Industry/Entity Type

Telecommunications

Colors

Designer to choose colors to be used in the design.

Requirements
Must have
• SEO Silo Look and Feel
• Current Colors
Should not have
• No stockphotos whatsoever. NONE.

```html
<!DOCTYPE html>
<html lang="en">
<head>
<meta charset="utf-8">
<title>Pollmark — Team</title>
<link href="https://fonts.googleapis.com/css2?family=Poppins:wght@300;400;500;600;700&display=swap" rel="stylesheet">
<style>
:root{
  --navy:#0c3865;
  --cyan:#13a8e2;
  --page:#f4f6fa;
  --blob:#e8ebf5;
  --text:#4a4f58;
  --muted:#8a9099;
  --avatar:#e6eef1;
  --white:#ffffff;
}
*{margin:0;padding:0;box-sizing:border-box}
html,body{width:1200px;height:2853px;overflow:hidden}
body{position:relative;background:var(--page);font-family:'Poppins',sans-serif;color:var(--text)}
.abs{position:absolute}
.bg-shapes{position:absolute;left:0;top:0}
.brand{left:141px;top:58px;display:flex;align-items:center;gap:8px;font-size:21px;font-weight:500;color:var(--navy)}
.brand .dot{width:18px;height:18px;border-radius:50%;background:var(--cyan)}
.nav{left:403px;top:78px;display:flex;gap:24px;font-size:12.5px;color:#2d3340}
.nav .active{color:var(--cyan);font-weight:600}
.phone{left:903px;top:63px;display:flex;align-items:center;gap:9px;font-weight:600;font-size:14px;color:var(--navy)}
.phone .ic{width:39px;height:39px;border-radius:50%;background:var(--cyan);display:flex;align-items:center;justify-content:center}
.hero-title{left:142px;top:202px;font-size:29px;font-weight:400;color:var(--navy)}
.hero-title span{color:var(--cyan)}
.rule{height:2px;width:34px;background:var(--cyan)}
.hero-copy{left:142px;top:272px;width:402px;font-size:11.6px;line-height:19.4px;letter-spacing:.2px;color:#3d4350}
.hero-copy p+p{margin-top:10px}
.btn{display:flex;align-items:center;justify-content:center;background:var(--navy);color:var(--white);border-radius:20px;font-size:14px;letter-spacing:.3px}
.hero-btn{left:141px;top:451px;width:261px;height:35px}
.hero-art{left:546px;top:131px;width:584px;height:353px;border-radius:30px;background:radial-gradient(ellipse at 50% 55%,#c9d6f5 0%,#dfe5f6 55%,rgba(232,235,245,0) 80%)}
.team-title{left:0;width:1200px;top:640px;text-align:center;font-size:30px;font-weight:700;color:var(--navy)}
.team-intro{left:170px;width:860px;top:712px;text-align:center;font-size:11.4px;line-height:19.4px;color:#4c525d}
.member{position:absolute;width:190px;text-align:center}
.member .pic{width:127px;height:127px;border-radius:50%;margin:0 auto;background:radial-gradient(circle at 50% 45%,#f6dd45 0 34%,#d9e4e8 35% 100%)}
.member .name{margin-top:18px;font-size:14px;font-weight:500;color:var(--navy)}
.member .role{margin-top:3px;font-size:13.5px;color:var(--muted);line-height:15px}
.footer-band{left:0;top:2480px;width:1200px;height:373px;background:var(--navy)}
.cta{left:211px;top:2374px;width:776px;height:213px;border-radius:107px;background:var(--cyan);text-align:center}
.cta h2{margin-top:52px;font-size:44px;font-weight:400;color:var(--white);letter-spacing:.5px}
.cta .btn{margin:18px auto 0;width:155px;height:34px;font-size:13.5px}
.f-head{font-size:17px;font-weight:600;color:var(--cyan)}
.f-links{font-size:12px;line-height:20px;color:var(--white)}
.f-contact{font-size:12.5px;line-height:22px;color:var(--white);display:flex;gap:8px}
.f-brand{left:950px;top:2700px;font-size:26px;font-weight:500;color:var(--white)}
.divider{left:139px;top:2806px;width:918px;height:1px;background:#2a5482}
.copy{left:0;width:1200px;top:2822px;text-align:center;font-size:12.5px;color:var(--white)}
</style>
</head>
<body>
<svg class="bg-shapes" width="1200" height="700" aria-hidden="true">
  <path d="M820 0 H1200 V600 C1100 620 920 600 800 480 C690 370 700 160 820 0Z" fill="var(--blob)"/>
</svg>

<div class="abs brand"><span class="dot"></span>Pollmark</div>
<nav class="abs nav"><span>Home</span><span>Services</span><span>Industries</span><span>Pricing</span><span class="active">Team</span><span>Blog</span><span>Contact Us</span></nav>
<div class="abs phone"><span class="ic"><svg width="16" height="16" viewBox="0 0 24 24"><path fill="#fff" d="M6.6 10.8a15 15 0 006.6 6.6l2.2-2.2a1 1 0 011-.25 11.4 11.4 0 003.6.57 1 1 0 011 1V20a1 1 0 01-1 1A17 17 0 013 4a1 1 0 011-1h3.5a1 1 0 011 1c0 1.25.2 2.45.57 3.57a1 1 0 01-.25 1z"/></svg></span>555-210-4477</div>

<h1 class="abs hero-title">We Are <span>Experts</span></h1>
<div class="abs rule" style="left:142px;top:249px"></div>
<div class="abs hero-copy">
  <p>Managing a call center is hard. We know. But if you really want to drive your business forward, you may need outside assistance. Pollmark brings on board a team of experts with multi-industry knowledge as well as best practices and ideas.</p>
  <p>Let Pollmark act as an extension of your team to listen and evaluate – and to provide actual, actionable feedback that will ensure compliance and quality that meets and exceeds your requirements.</p>
</div>
<div class="abs btn hero-btn">CONTACT OUR TEAM TODAY</div>
<div class="abs hero-art" role="img" aria-label="Illustration of a team working at laptops around a red desk with chat bubbles and a presentation board"></div>

<h2 class="abs team-title">Meet The Team</h2>
<div class="abs rule" style="left:583px;top:690px"></div>
<p class="abs team-intro">Pollmark's outstanding cast of team member's are relentless in their pursuit of perfection. They realize that quality means everything to their customers, and their customers mean everything to them. You can count on their motivated team of professionals to work tirelessly for you, and with decades of combined experience in the customer service and call quality industries, you can confidently know they have the capacity and wherewithal to do just that.</p>

<!-- row 1 -->
<div class="member" style="left:109px;top:833px"><div class="pic" role="img" aria-label="Cartoon portrait of Owen Farrel"></div><div class="name">Owen Farrel</div><div class="role">CEO</div></div>
<div class="member" style="left:306px;top:833px"><div class="pic" role="img" aria-label="Cartoon portrait of Grant Pellow"></div><div class="name">Grant Pellow</div><div class="role">COO</div></div>
<div class="member" style="left:503px;top:833px"><div class="pic" role="img" aria-label="Cartoon portrait of Dale Wren"></div><div class="name">Dale Wren</div><div class="role">CTO</div></div>
<div class="member" style="left:701px;top:833px"><div class="pic" role="img" aria-label="Cartoon portrait of Colin Ashby"></div><div class="name">Colin Ashby</div><div class="role">VP of Client Services</div></div>
<div class="member" style="left:898px;top:833px"><div class="pic" role="img" aria-label="Cartoon portrait of Ross Keller"></div><div class="name">Ross Keller</div><div class="role">Director Of<br>International Sales</div></div>
<!-- row 2 -->
<div class="member" style="left:109px;top:1086px"><div class="pic" role="img" aria-label="Cartoon portrait of Evan Marsh"></div><div class="name">Evan Marsh</div><div class="role">Director of<br>Legal Affairs</div></div>
<div class="member" style="left:306px;top:1086px"><div class="pic" role="img" aria-label="Cartoon portrait of Peter Hallam"></div><div class="name">Peter Hallam</div><div class="role">RED LEADER</div></div>
<div class="member" style="left:503px;top:1086px"><div class="pic" role="img" aria-label="Cartoon portrait of Toby Lund"></div><div class="name">Toby Lund</div><div class="role">Toby Lund</div></div>
<div class="member" style="left:701px;top:1086px"><div class="pic" role="img" aria-label="Cartoon portrait of Nadia Ortega"></div><div class="name">Nadia Ortega</div><div class="role">Operations<br>Manager</div></div>
<div class="member" style="left:898px;top:1086px"><div class="pic" role="img" aria-label="Cartoon portrait of Luke Brandt"></div><div class="name">Luke Brandt</div><div class="role">Senior Developer</div></div>
<!-- row 3 -->
<div class="member" style="left:109px;top:1336px"><div class="pic" role="img" aria-label="Cartoon portrait of Rina Tabor"></div><div class="name">Rina Tabor</div><div class="role">Training Manager</div></div>
<div class="member" style="left:306px;top:1336px"><div class="pic" role="img" aria-label="Cartoon portrait of Marco Delvin"></div><div class="name">Marco Delvin</div><div class="role">Team Lead</div></div>
<div class="member" style="left:503px;top:1336px"><div class="pic" role="img" aria-label="Cartoon portrait of Ivy Carden"></div><div class="name">Ivy Carden</div><div class="role">Team Lead</div></div>
<div class="member" style="left:701px;top:1336px"><div class="pic" role="img" aria-label="Cartoon portrait of Leo Varga"></div><div class="name">Leo Varga</div><div class="role">Team Lead</div></div>
<div class="member" style="left:898px;top:1336px"><div class="pic" role="img" aria-label="Cartoon portrait of Helen Ward"></div><div class="name">Helen Ward</div><div class="role">Team Lead</div></div>
<!-- row 4 -->
<div class="member" style="left:109px;top:1568px"><div class="pic" role="img" aria-label="Cartoon portrait of Clara Novak"></div><div class="name">Clara Novak</div><div class="role">Team Lead</div></div>
<div class="member" style="left:306px;top:1568px"><div class="pic" role="img" aria-label="Cartoon portrait of Felix Orman"></div><div class="name">Felix Orman</div><div class="role">Operations Manager</div></div>
<div class="member" style="left:503px;top:1568px"><div class="pic" role="img" aria-label="Cartoon portrait of Noel Santar"></div><div class="name">Noel Santar</div><div class="role">IT-Manager</div></div>
<div class="member" style="left:701px;top:1568px"><div class="pic" role="img" aria-label="Cartoon portrait of the IT manager"></div><div class="name">IT-Manager</div><div class="role">Team Lead</div></div>
<div class="member" style="left:898px;top:1568px"><div class="pic" role="img" aria-label="Cartoon portrait of Mia Doral"></div><div class="name">Mia Doral</div><div class="role">Team Lead</div></div>
<!-- row 5 -->
<div class="member" style="left:109px;top:1801px"><div class="pic" role="img" aria-label="Cartoon portrait of Lena Orman"></div><div class="name">Lena Orman</div><div class="role">Hiring Manager</div></div>
<div class="member" style="left:306px;top:1801px"><div class="pic" role="img" aria-label="Cartoon portrait of Kai Lin"></div><div class="name">Kai Lin</div><div class="role">Team Lead</div></div>
<div class="member" style="left:503px;top:1801px"><div class="pic" role="img" aria-label="Cartoon portrait of Olena Marchuk"></div><div class="name">Olena Marchuk</div><div class="role">Project Manager</div></div>
<div class="member" style="left:701px;top:1801px"><div class="pic" role="img" aria-label="Cartoon portrait of Daria Levchenko"></div><div class="name">Daria Levchenko</div><div class="role">Front-<br>End Developer</div></div>
<div class="member" style="left:898px;top:1801px"><div class="pic" role="img" aria-label="Cartoon portrait of Taras Bondar"></div><div class="name">Taras Bondar</div><div class="role">Front-<br>End Developer</div></div>
<!-- row 6 -->
<div class="member" style="left:109px;top:2050px"><div class="pic" role="img" aria-label="Cartoon portrait of Ilya Petrov"></div><div class="name">Ilya Petrov</div><div class="role">Designer</div></div>
<div class="member" style="left:306px;top:2050px"><div class="pic" role="img" aria-label="Cartoon portrait of Joel Manalo"></div><div class="name">Joel Manalo</div><div class="role">Web Developer</div></div>
<div class="member" style="left:503px;top:2050px"><div class="pic" role="img" aria-label="Cartoon portrait of Bohdan Kovac"></div><div class="name">Bohdan Kovac</div><div class="role">Back-<br>End Developer</div></div>
<div class="member" style="left:701px;top:2050px"><div class="pic" role="img" aria-label="Cartoon of the brown office dog" style="background:radial-gradient(circle at 50% 50%,#b9703f 0 34%,#d9e4e8 35% 100%)"></div><div class="name">Maple Hallam</div><div class="role">Office Dog</div></div>
<div class="member" style="left:898px;top:2050px"><div class="pic" role="img" aria-label="Cartoon of the black office dog" style="background:radial-gradient(circle at 50% 50%,#1d1d1f 0 34%,#d9e4e8 35% 100%)"></div><div class="name">Pepper Lund</div><div class="role">Office Dog</div></div>

<div class="abs footer-band"></div>
<div class="abs cta"><h2>Give Us A Shout</h2><div class="btn">GET IN TOUCH</div></div>

<div class="abs f-head" style="left:139px;top:2640px">Quick Links</div>
<div class="abs f-links" style="left:139px;top:2676px">Home<br>Services<br>System Details<br>Pricing</div>
<div class="abs f-links" style="left:294px;top:2676px">Team<br>Blog<br>Contact Us<br>Login</div>
<div class="abs f-head" style="left:460px;top:2640px">Contact Us</div>
<div class="abs f-contact" style="left:462px;top:2676px"><svg width="11" height="14" viewBox="0 0 12 16" style="margin-top:5px"><path fill="#fff" d="M6 0a6 6 0 00-6 6c0 4.5 6 10 6 10s6-5.5 6-10a6 6 0 00-6-6zm0 8.5A2.5 2.5 0 116 3.5a2.5 2.5 0 010 5z"/></svg><span>4810 Harlow Ave.<br>Fairbrook, CA 90412</span></div>
<div class="abs f-contact" style="left:660px;top:2676px"><svg width="13" height="13" viewBox="0 0 24 24" style="margin-top:5px"><path fill="#fff" d="M6.6 10.8a15 15 0 006.6 6.6l2.2-2.2a1 1 0 011-.25 11.4 11.4 0 003.6.57 1 1 0 011 1V20a1 1 0 01-1 1A17 17 0 013 4a1 1 0 011-1h3.5a1 1 0 011 1c0 1.25.2 2.45.57 3.57a1 1 0 01-.25 1z"/></svg><span>555-210-4477</span></div>
<div class="abs f-contact" style="left:660px;top:2711px"><svg width="13" height="11" viewBox="0 0 24 18" style="margin-top:6px"><path fill="#fff" d="M0 0h24v18H0z"/><path d="M1 1l11 9 11-9" stroke="#0c3865" stroke-width="2" fill="none"/></svg><span>hello@pollmark.com</span></div>
<div class="abs f-brand">Pollmark</div>
<div class="abs divider"></div>
<div class="abs copy">Copyright © 2019 POLLMARK. All Rights Reserved.</div>
</body>
</html>
```